Fresh, modern, fun business card for pediatric dental practice

Need a business card for fresh, modern, fun pediatric dental practice

Clean look that matches our website's font and colors

We prefer the look of curved corners on business cards

Target Market(s)

parents (mothers) of young children, professionals, mid-high class

Industry/Entity Type

Dental

Contact Information for Business Card

Maplebrook Pediatric Dentistry
482 Quarry Lane
Suite 517
Alderwick, ST 00000
717.555.0193
www.maplebrookkidsdental.example

Mei-Ran Tsai, DMD
Corinne Walbeck, DMD
(we are working on our email address, but we would like that on the card as well)

Font styles to use
Sans Serif

Requirements
Must have
• All info; we would also like to make cards for individual staff members
• colors from our website and color palatte, attatched
• use same font and design as website for branding
Nice to have
• clean, simple card that has a pop of color
• we would like to see a few designs with our tag line "where smiles get brighter"
• we are not sure if we want to have it on there or not
• we would like to see a few designs incorporating the ribbon graphic on our website where the word WELCOME is

```html
<!DOCTYPE html>
<html lang="en">
<head>
<meta charset="utf-8">
<title>Maplebrook Pediatric Dentistry – Business Card</title>
<link rel="stylesheet" href="https://fonts.googleapis.com/css2?family=PT+Sans:wght@400;700&display=swap">
<style>
  :root {
    --backdrop: #2a2a2a;
    --card: #121212;
    --card-edge: #1c1c1c;
    --sun-yellow: #f7b51d;
    --text-white: #eeeeee;
    --berry: #c2268a;
    --divider: #262626;
  }
  * { margin: 0; padding: 0; box-sizing: border-box; }
  html, body {
    width: 1200px; height: 900px; overflow: hidden;
    background: var(--backdrop);
    font-family: "PT Sans", sans-serif;
  }
  .stage {
    position: relative; width: 1200px; height: 900px;
    display: flex; align-items: center; justify-content: center; gap: 40px;
  }
  .card {
    position: relative;
    width: 540px; height: 309px;
    background: var(--card);
    border-radius: 22px;
    box-shadow: 0 0 0 1px var(--card-edge);
    overflow: hidden;
  }
  /* contact side */
  .card--contact { display: flex; }
  .brand-panel {
    width: 200px; height: 100%;
    display: flex; flex-direction: column; align-items: center; justify-content: center; gap: 14px;
    border-right: 1px solid var(--divider);
  }
  .brand-panel__dot {
    width: 70px; height: 70px; border-radius: 50%;
    border: 6px solid var(--sun-yellow);
  }
  .brand-panel__name {
    color: var(--sun-yellow); font-weight: 700; font-size: 22px;
  }
  .details { padding: 34px 0 0 26px; color: var(--text-white); }
  .doctors { color: var(--sun-yellow); font-size: 22px; line-height: 1.05; }
  .doctors small { font-size: 13px; }
  .practice {
    color: var(--sun-yellow); font-weight: 700; font-size: 15px; margin-top: 12px;
  }
  .address { font-size: 14px; line-height: 1.35; margin-top: 2px; }
  .contact-list { list-style: none; margin-top: 16px; font-size: 13.5px; line-height: 1.45; }
  .contact-list li { display: flex; align-items: center; gap: 10px; }
  .contact-list svg { width: 11px; height: 11px; flex: none; }
  .icon-fill { fill: var(--sun-yellow); }
  .icon-mail rect { fill: var(--sun-yellow); }
  .icon-mail path { fill: none; stroke: var(--card); stroke-width: 2.5; }
  /* logo side */
  .card--logo { display: flex; align-items: center; justify-content: center; }
  .logo-lockup { display: flex; align-items: center; gap: 16px; }
  .logo-lockup__dot {
    width: 34px; height: 34px; border-radius: 50%; background: var(--berry);
  }
  .logo-lockup__name {
    color: var(--sun-yellow); font-weight: 700; font-size: 36px; line-height: 1.05;
  }
</style>
</head>
<body>
<main class="stage">
  <section class="card card--contact">
    <div class="brand-panel">
      <span class="brand-panel__dot"></span>
      <span class="brand-panel__name">Maplebrook</span>
    </div>
    <div class="details">
      <p class="doctors">Mei-Ran Tsai, <small>DMD</small><br>Corinne Walbeck, <small>DMD</small></p>
      <p class="practice">Maplebrook Pediatric Dentistry</p>
      <p class="address">482 Quarry Lane Suite 517<br>Alderwick, ST 00000</p>
      <ul class="contact-list">
        <li><svg class="icon-fill" viewBox="0 0 24 24"><path d="M6.6 10.8a15 15 0 0 0 6.6 6.6l2.2-2.2c.3-.3.7-.4 1-.2 1.1.4 2.3.6 3.6.6.6 0 1 .4 1 1V20c0 .6-.4 1-1 1A17 17 0 0 1 3 4c0-.6.4-1 1-1h3.5c.6 0 1 .4 1 1 0 1.3.2 2.5.6 3.6.1.3 0 .7-.2 1z"/></svg>555.555.0193</li>
        <li><svg class="icon-mail" viewBox="0 0 24 24"><rect x="2" y="5" width="20" height="14"/><path d="M2 5l10 8 10-8"/></svg>Mei-ran@maplebrookkidsdental.example</li>
        <li><svg class="icon-mail" viewBox="0 0 24 24"><rect x="2" y="5" width="20" height="14"/><path d="M2 5l10 8 10-8"/></svg>Corinne@maplebrookkidsdental.example</li>
        <li><svg class="icon-fill" viewBox="0 0 24 24"><circle cx="12" cy="12" r="10"/></svg>www.maplebrookkidsdental.example</li>
      </ul>
    </div>
  </section>
  <section class="card card--logo">
    <div class="logo-lockup">
      <span class="logo-lockup__dot"></span>
      <span class="logo-lockup__name">Maplebrook<br>Pediatric Dentistry</span>
    </div>
  </section>
</main>
</body>
</html>
```